Agrarhandel benötigt Homepage
Zielgruppe
Wir sind ein Agrarhandel mit einem Warenumschlagslager im Sinne eines klassischen Einzelhandels und vertreiben Produkte an Landwirte.
Wir vertreiben folgende Hauptproduktgruppen:
Einzelfuttermittel
wie z.B. Sojaexktraktionsschrot. Die einzelnen Produkte könnten z.B. wie die Futtermittel auf folgender Seite dargestellt werden (https://www.kornprobe-beispiel.eu/de/produkt/trelomixan)
Mischfuttermittel
Hier bieten wir unseren Kunden an, individuelles Mischfutter auf Basis unserer Einzelfuttermittel herzustellen.
Weitere Details und weitere Produktbereiche habe ich in einer Powerpoint-Übersicht dargestellt.
Neben diesen Produkten wollen wir uns als Familienunternehmen selbst vorstellen. Zudem betreiben wir in unserer Familie zusätzlich einen Milchviehbetrieb den wir ebenfalls hervorheben möchten, da wir unseren Kunden gegenüber einerseits als Zulieferer aber auch als Kollege auftreten wollen.
Einzelfuttermittel: Hier können wir durch unsere Unabhängigkeit punkten, da wir nicht abhängig von bestimmten Lieferanten sind und dementsprechend unabhängig beraten können. Wir untersuchen im Vergleich zu unseren Wettbewerben die Qualität der Futtermittel bis ins Detail und können daher eine Transparenz bieten, die Konkurrenten in der Regel nicht bieten können. Unser Warenumschlagsplatz mit moderner Technik ermöglicht es uns äußerst kosteneffizient die Waren umschlagen und ausliefern zu können.
Mischfuttermittel: Auf Basis der vorhandenen Einzelfuttermittel stellen wir je nach Kundenwunsch individuelle Mischfutter her. Wir arbeiten mit offenen Deklarationen, sodass unsere Kunden jederzeit nachvollziehen können, ob auch die Einzelfuttermittel verwendet wurden, die sie bestellt haben und keine billigen Ersatzprodukte verwendet wurden.
Zudem sind wir BT und HUPA zertifiziert. Die aktuellen für unser Unternehmen ausgestellten Zertifikate müssen für unsere Kunden als Download zur Verfügung stehen. Statt dem HUPA-Logo bitte das ..
Aufgabenstellung
Wir möchten gerne ein zeitgemäße Homepage, jedoch muss auch berücksichtigt werden, dass unsere Kunden eher konservativ denken.

```html
<!DOCTYPE html>
<html lang="de">
<head>
<meta charset="utf-8">
<title>Talgrund Agrar – Startseite</title>
<link rel="stylesheet" href="https://fonts.googleapis.com/css2?family=Inter:ital,wght@0,400;0,500;0,600;0,700;0,800;1,600&display=swap">
<style>
:root{
  --green:#44651a;
  --orange:#f3a712;
  --yellow:#f4cb1f;
  --dark:#252525;
  --grey:#dcdcdc;
  --white:#ffffff;
  --ink:#111111;
  --wood:#8a6f55;
}
*{box-sizing:border-box;margin:0;padding:0}
html,body{width:734px;height:1200px;overflow:hidden}
body{position:relative;background:var(--white);font-family:"Inter",sans-serif;color:var(--ink)}
.abs{position:absolute}

/* header */
.header{left:0;top:0;width:734px;height:70px;background:var(--green)}
.header__accent{left:0;top:0;width:43px;height:70px;background:var(--orange)}
.header__gap{left:43px;top:0;width:9px;height:70px;background:var(--grey)}
.brand{left:70px;top:24px;display:flex;align-items:center;gap:5px;color:var(--orange);font-weight:700;font-size:10px}
.brand__dot{width:14px;height:14px;border-radius:50%;background:var(--orange)}
.nav{right:48px;top:33px;display:flex;gap:10px;font-size:8px;font-weight:700;color:var(--white);letter-spacing:.1px}
.nav .is-active{color:var(--orange)}
.search{right:18px;top:30px}
.header__line{left:0;top:75px;width:734px;height:5px;background:var(--grey)}

/* hero */
.hero{left:0;top:84px;width:734px;height:188px;background:linear-gradient(180deg,#6e5643,#a58a70 45%,#7d6450)}
.hero__box{left:118px;top:27px;width:497px;height:121px;border:1px solid rgba(255,255,255,.55);border-radius:10px;background:rgba(200,185,170,.45);padding:11px 8px;text-align:center;font-size:12.3px;font-weight:500;line-height:14.8px}

/* features */
.features__bg{left:0;top:290px}
.feature{width:126px;text-align:center}
.feature__title{font-size:12px;font-weight:500;margin-top:6px}
.feature__text{position:absolute;top:74px;left:0;width:126px;font-size:10.8px;line-height:12.3px}

/* why section */
.why__bg{left:0;top:494px}
.why__title{left:178px;top:527px;color:var(--white);font-size:19px;font-weight:400}
.why__lead{left:176px;top:561px;width:240px;color:var(--white);font-size:5.5px;line-height:7px}
.point{color:var(--white);width:110px;padding-left:19px}
.point::before{content:"";position:absolute;left:0;top:0;width:11px;height:11px;border-radius:50%;background:var(--yellow)}
.point b{display:block;font-size:6px;font-weight:600;margin-bottom:4px}
.point span{display:block;font-size:5.3px;line-height:6.6px}
.why__button{left:322px;top:689px;width:56px;height:15px;border-radius:8px;background:var(--yellow)}
.why__frame{left:452px;top:527px;width:250px;height:168px;border-radius:6px;background:var(--yellow)}
.why__photo{left:444px;top:536px;width:250px;height:169px;background:linear-gradient(160deg,#d99a4a,#a86a2a 50%,#6e4318)}

/* certificates */
.badge-hupa{left:62px;top:836px;width:82px;height:81px;border-radius:5px;background:#4aa232;border:2px solid #e6efe0}
.cert-and{left:186px;top:860px;font-size:12px;font-weight:600}
.badge-bt{left:254px;top:836px;width:65px;height:74px;border:1px solid #1b5fa8;background:#eef4fb}
.cert-label{left:148px;top:923px;font-size:20px;font-weight:600;font-style:italic}
.download{left:446px;top:881px;width:226px;height:61px;border-radius:30px;background:var(--orange);box-shadow:4px 4px 6px rgba(0,0,0,.25);display:flex;align-items:center;justify-content:center;text-align:center;font-size:16.5px;font-weight:800;line-height:20px;color:var(--ink)}

/* footer */
.footer{left:0;top:967px;width:734px;height:203px;background:var(--dark)}
.footer__brand{left:92px;top:1038px;display:flex;align-items:center;gap:6px;color:var(--orange);font-weight:700;font-size:13px}
.footer__brand i{width:16px;height:16px;border-radius:50%;background:var(--orange)}
.divider{width:2px;height:88px;background:var(--white)}
.divider::before,.divider::after{content:"";position:absolute;left:-2px;width:6px;height:6px;border-radius:50%;background:var(--white)}
.divider::before{top:-3px}.divider::after{bottom:-3px}
.newsletter__title{left:242px;top:1009px;color:var(--white);font-size:12px;font-weight:600}
.newsletter__title b{font-size:16px;font-weight:700}
.field{height:14px;background:var(--grey);font-size:5.8px;font-weight:500;padding:4px 5px;color:#333}
.submit{left:416px;top:1061px;width:77px;height:14px;border-radius:4px;background:var(--yellow);font-size:7px;font-weight:700;text-align:center;line-height:14px}
.contact{left:537px;top:1037px;color:var(--white);font-size:6.5px;line-height:11px}
.contact div{display:flex;align-items:center;gap:7px}
.reach{left:279px;top:1103px;font-size:12px;font-weight:700;color:var(--orange)}
.reach span{color:var(--white)}
.chat{left:438px;top:1097px;width:31px;height:31px;border-radius:8px;background:#2ec24a}
.socials{left:340px;top:1149px;display:flex;gap:3px}
.socials i{width:12px;height:12px;border-radius:2px;background:var(--white)}
.copyright{left:0;top:1170px;width:734px;height:30px;background:var(--yellow);font-size:7px;font-weight:500;text-align:center;line-height:30px}
</style>
</head>
<body>

<header>
  <div class="abs header"></div>
  <div class="abs header__accent"></div>
  <div class="abs header__gap"></div>
  <div class="abs brand"><span class="brand__dot"></span>Talgrund Agrar</div>
  <nav class="abs nav">
    <span class="is-active">LANDWIRT</span><span>GESCHÄFTSPARTNER</span><span>LIEFERANTEN</span><span>PRODUKTE</span><span>FIRMENPRÄSENTATION</span>
  </nav>
  <svg class="abs search" width="14" height="14" viewBox="0 0 14 14"><circle cx="5.5" cy="5.5" r="4.3" fill="none" stroke="#fff" stroke-width="1.3"/><line x1="8.7" y1="8.7" x2="13" y2="13" stroke="#fff" stroke-width="1.5"/></svg>
  <div class="abs header__line"></div>
</header>

<section>
  <div class="abs hero" role="img" aria-label="Holzbretter-Hintergrund"></div>
  <div class="abs hero__box" style="top:111px">Excepteur sint occaecat cupidatat non proident, sunt in culpa qExcepteur sint occaecat cupidatat non proident, sunt in culpa qui officia deserunt mollit anim id esExcepteur sint occaecat cupidatat non proident, sunt in culpa qui officia deserunt mollit anim id esExcepteur sint occaecat cupidatat non proident, sunt in culpa qui officia deserunt mollit anim id Excepteur sint occaecat cupidatat non proident, sunt in culpa qui officia deserunt mollit anim id es officia deserunt mollit anim id es</div>
</section>

<section>
  <svg class="abs features__bg" width="734" height="190" viewBox="0 0 734 190">
    <path d="M95 83 Q100 66 125 64 L630 3 Q649 1 649 20 L649 160 Q649 184 625 184 L120 184 Q95 184 95 160 Z" fill="var(--yellow)"/>
  </svg>
  <div class="abs feature" style="left:108px;top:298px">
    <svg width="28" height="28" viewBox="0 0 28 28"><path d="M14 2 L25 6 V13 C25 20 20 24 14 26 C8 24 3 20 3 13 V6 Z" fill="#111"/><path d="M14 19 V12 M14 14 C11 14 10 11 10 9 C12 9 14 11 14 14 C14 11 16 9 18 9 C18 11 17 14 14 14" stroke="#fff" stroke-width="1.4" fill="none"/></svg>
    <div class="feature__title">Lorem Ipsum</div>
    <div class="feature__text">Excepteur sint occaecat cupidatat non proident, sunt in Excepteur sint occaecat cupidatat non Excepteur sint occaecat cupidatat non proident, sunt in culpa , sunt in culpa</div>
  </div>
  <div class="abs feature" style="left:240px;top:296px">
    <svg width="28" height="32" viewBox="0 0 28 32"><circle cx="14" cy="12" r="11" fill="#111"/><circle cx="14" cy="12" r="7" fill="none" stroke="#fff" stroke-width="1.3"/><path d="M10.5 12 L13 14.5 L17.5 9.5" stroke="#fff" stroke-width="1.6" fill="none"/><path d="M8 20 L4 30 L8 28 L10 31 L13 22 M20 20 L24 30 L20 28 L18 31 L15 22" fill="#111"/></svg>
    <div class="feature__title" style="margin-top:2px">Lorem Ipsum</div>
    <div class="feature__text">Excepteur sint occaecat cupidatat non proident, sunt in Excepteur sint occaecat cupidatat non Excepteur sint occaecat cupidatat non proident, sunt in culpa , sunt in culpa</div>
  </div>
  <div class="abs feature" style="left:378px;top:298px">
    <svg width="28" height="28" viewBox="0 0 28 28"><circle cx="14" cy="14" r="12" fill="#111"/><path d="M14 19 C9 19 7 15 7 12 C10 12 14 14 14 19 C14 14 18 12 21 12 C21 15 19 19 14 19" fill="#fff"/></svg>
    <div class="feature__title">Lorem Ipsum</div>
    <div class="feature__text">Excepteur sint occaecat cupidatat non proident, sunt in Excepteur sint occaecat cupidatat non Excepteur sint occaecat cupidatat non proident, sunt in culpa , sunt in culpa</div>
  </div>
  <div class="abs feature" style="left:507px;top:294px">
    <svg width="32" height="32" viewBox="0 0 32 32"><path d="M11 4 L16 2 L21 4 V9 C21 12 18 14 16 15 C14 14 11 12 11 9 Z" fill="none" stroke="#111" stroke-width="1.2"/><path d="M13.5 8 L15.5 10 L18.5 6.5" stroke="#111" stroke-width="1.2" fill="none"/><path d="M2 17 L9 13 L16 17 L23 13 L30 17 L26 24 L20 29 L12 29 L6 24 Z" fill="#111"/></svg>
    <div class="feature__title" style="margin-top:2px">Lorem Ipsum</div>
    <div class="feature__text" style="left:3px">Excepteur sint occaecat cupidatat non proident, sunt in Excepteur sint occaecat cupidatat non Excepteur sint occaecat cupidatat non proident, sunt in culpa , sunt in culpa</div>
  </div>
</section>

<section>
  <svg class="abs why__bg" width="734" height="318" viewBox="0 0 734 318">
    <rect width="734" height="318" fill="var(--dark)"/>
    <polygon points="0,189 734,286 734,318 0,318" fill="var(--white)"/>
    <polygon points="0,247 734,306 734,318 0,318" fill="var(--yellow)"/>
  </svg>
  <h2 class="abs why__title">Warum Uns Wählen?</h2>
  <p class="abs why__lead">Excepteur sint occaecat cupidatat non proident, sunt in culpa qui officia deserunt mollit anim id es</p>
  <div class="abs point" style="left:176px;top:589px"><b>Lorem Ipsum</b><span>Excepteur sint occaecat cupidatat non proident, sunt in culpa</span></div>
  <div class="abs point" style="left:289px;top:589px"><b>Lorem Ipsum</b><span>Excepteur sint occaecat cupidatat non proident, sunt in culpa</span></div>
  <div class="abs point" style="left:176px;top:636px"><b>Lorem Ipsum</b><span>Excepteur sint occaecat cupidatat non proident, sunt in culpa</span></div>
  <div class="abs point" style="left:289px;top:636px"><b>Lorem Ipsum</b><span>Excepteur sint occaecat cupidatat non proident, sunt in culpa</span></div>
  <div class="abs why__button"></div>
  <div class="abs why__frame"></div>
  <div class="abs why__photo" role="img" aria-label="Foto: Mähdrescher bei der Getreideernte im Abendlicht"></div>
</section>

<section>
  <div class="abs badge-hupa" role="img" aria-label="Zertifizierungssiegel HUPA"></div>
  <div class="abs cert-and">und</div>
  <div class="abs badge-bt" role="img" aria-label="Zertifizierungssiegel BT"></div>
  <div class="abs cert-label">zertifiziert</div>
  <div class="abs download">HERUNTERLADEN<br>ZERTIFIKAT</div>
</section>

<footer>
  <div class="abs footer"></div>
  <div class="abs footer__brand"><i></i>Talgrund Agrar</div>
  <div class="abs divider" style="left:217px;top:1006px"></div>
  <div class="abs divider" style="left:515px;top:1006px"></div>
  <div class="abs newsletter__title">Abonnieren Sie Unseren <b>Newsletter</b></div>
  <div class="abs field" style="left:242px;top:1032px;width:77px">Name</div>
  <div class="abs field" style="left:329px;top:1032px;width:77px">Email</div>
  <div class="abs field" style="left:416px;top:1032px;width:77px">Telefonnummer</div>
  <div class="abs field" style="left:242px;top:1059px;width:164px;height:20px;padding-top:7px">Nachricht</div>
  <div class="abs submit">SCHICKEN</div>
  <div class="abs contact">
    <div><svg width="6" height="8" viewBox="0 0 6 8"><path d="M3 0 C1.3 0 0 1.3 0 3 C0 5 3 8 3 8 C3 8 6 5 6 3 C6 1.3 4.7 0 3 0 Z" fill="#fff"/><circle cx="3" cy="3" r="1" fill="var(--dark)"/></svg>Locatins</div>
    <div><svg width="7" height="7" viewBox="0 0 7 7"><circle cx="3.5" cy="3.5" r="3.5" fill="#fff"/><path d="M2 2 L3 3.5 L4.5 5" stroke="var(--dark)" stroke-width="1"/></svg>+49 7000 112233</div>
    <div><svg width="7" height="5" viewBox="0 0 7 5"><rect width="7" height="5" fill="#fff"/><path d="M0 0 L3.5 2.8 L7 0" stroke="var(--dark)" stroke-width=".7" fill="none"/></svg>info@talgrund-agrar.de</div>
  </div>
  <div class="abs reach">Kontaktieren Sie Uns <span>per</span></div>
  <div class="abs chat"></div>
  <div class="abs socials"><i></i><i></i><i></i><i></i></div>
  <div class="abs copyright">Copyright 2023 All Right Reserved</div>
</footer>

</body>
</html>
```